Web Design for Independent Pet Supply shop.

Larch Critter Depot is a locally owned and operated premium natural pet food store and supply company with 2 thriving retail stores in Bend, Oregon, and a home delivery service. The pet food offered is the best on the market and may be described as “holistic”. Also on offer is a vast selection of toys, training tools, treats, and other supplies, as well as dog washing services that range from "do-it yourself" to "spa." Current site: LarchCritterDepot.com. They need a new, updated and responsive site.
Likes:
Tovanels.com: Natural colors, not loud, pages in motion, simple & clean but very informative.
Dorvikmerin.com: Everything in simple big colorful blocks. The specials run across the top and in motion. This site looks very professional but simple. The information is available several different places.
Plenharvest.com: Again big blocks through out. Very Fun and inviting. Tons of information with videos and recipes and testimonials. Pleasant feel and colors as well.
Dislikes:
Furlix.com: Looks cheap, hate the colors, very busy and over whelming. Hate the old style header bar going across with options. Too many printed words instead of fun images.
Colors should be "natural" tones, warm and soothing. Deep dark blue and greys with earthy wood color.
Do Not Use: Blue violet, violet, red violet

```html
<!DOCTYPE html>
<html lang="en">
<head>
<meta charset="utf-8">
<title>Larch Critter Depot</title>
<link href="https://fonts.googleapis.com/css2?family=Open+Sans:wght@400;600;700&family=Ubuntu:wght@500;700&display=swap" rel="stylesheet">
<style>
:root{
  --wood:#6a4322;
  --wood-dark:#5a381b;
  --sand:#f1e1c3;
  --blue:#1b5db4;
  --blue-deep:#134a98;
  --ink:#3b3026;
  --gold:#f0a83a;
  --white:#ffffff;
  --night:#1d1d1d;
}
*{box-sizing:border-box;margin:0;padding:0}
html,body{width:741px;height:1200px;overflow:hidden}
body{position:relative;background:var(--sand);font-family:"Open Sans",sans-serif;color:var(--ink)}
.abs{position:absolute}
.topbar{left:0;top:0;width:741px;height:41px;background:var(--wood)}
.social{display:flex;gap:5px}
.social span{width:18px;height:18px;border-radius:50%;background:var(--blue);display:block}
.topbar .social{position:absolute;left:398px;top:11px}
.search{left:537px;top:10px;width:158px;height:21px;background:var(--white);border-radius:2px;font-size:8px;color:#777;padding:5px 8px}
.search svg{position:absolute;right:6px;top:5px}
.brandband{left:0;top:41px;width:741px;height:32px;background:var(--white)}
.logo{display:flex;align-items:center;gap:6px;font-family:"Open Sans",sans-serif;font-weight:700;color:#b8853f;font-size:17px}
.logo i{width:26px;height:26px;border-radius:50%;background:#b8853f;display:block}
.brandband .logo{position:absolute;left:46px;top:3px}
.nav{left:0;top:73px;width:741px;height:37px;background:linear-gradient(var(--blue),var(--blue-deep))}
.nav a{position:absolute;top:13px;font-size:8.5px;font-weight:600;color:var(--white);text-decoration:none}
.hero{left:46px;top:120px;width:649px;height:236px;background:var(--white);padding:3px}
.hero-photo{width:100%;height:100%;background:linear-gradient(100deg,#efe9e2 0%,#ddd0c0 45%,#c9a66e 70%,#a8a29a 100%)}
.hero h1{position:absolute;left:24px;top:88px;font-size:20.5px;line-height:24px;font-weight:700;color:#6a4322;letter-spacing:.3px}
.hero h1 b{color:var(--blue)}
.dots{position:absolute;left:33px;top:210px;display:flex;gap:5px}
.dots span{width:9px;height:9px;border-radius:50%;background:var(--white)}
.dots span:first-child{background:var(--blue)}
.card{top:375px;width:204px;height:134px;background:var(--wood);box-shadow:0 8px 8px -4px rgba(0,0,0,.35);padding:0 9px}
.card h3{display:flex;align-items:center;gap:9px;margin-top:15px;font-size:10px;font-weight:600;color:var(--white)}
.card h3 i{width:19px;height:19px;border-radius:50%;border:2px solid var(--white);display:block}
.card p{margin-top:8px;padding-right:8px;font-size:7.6px;line-height:15px;color:#f3e8d8;height:48px}
.btn{display:inline-block;background:var(--blue);color:var(--white);font-size:8px;font-weight:600;padding:7px 10px;border-radius:1px}
.card .btn{position:absolute;left:9px;top:95px}
.rule{left:46px;top:538px;width:649px;height:1px;background:#c9b08a}
.section-title{left:46px;top:555px;font-size:15px;font-weight:600;color:#3a2b1f}
.blog-photo{left:46px;top:586px;width:428px;height:128px;background:linear-gradient(90deg,#4f5152,#6d6a62 30%,#3f4142 50%,#5c5a55 75%,#3b3d3e)}
.blog-title{left:46px;top:728px;font-family:"Ubuntu",sans-serif;font-size:17px;font-weight:500;color:var(--blue)}
.blog-text{left:46px;top:759px;width:428px;font-size:8.6px;line-height:15px;color:#3b3026}
.blog-text p+p{margin-top:6px}
.newsletter{left:490px;top:559px;width:205px;height:99px;background:linear-gradient(var(--blue),var(--blue-deep));padding:13px 12px}
.newsletter h2{font-family:"Ubuntu",sans-serif;font-size:15px;font-weight:500;color:var(--white)}
.newsletter .field{margin-top:9px;height:25px;background:var(--white);font-size:7.5px;color:#666;padding:8px 9px}
.dark-btn{position:absolute;right:15px;top:72px;background:#1c1c1c;color:var(--white);font-size:7.5px;font-weight:600;padding:6px 10px;border-radius:2px}
.tile{left:490px;width:205px;height:119px;overflow:hidden}
.tile .photo{position:absolute;inset:0}
.tile .band{position:absolute;left:0;bottom:0;width:100%;height:43px;background:var(--blue)}
.tile .badge{position:absolute;left:12px;bottom:10px;width:46px;height:46px;border-radius:50%;background:var(--white);border:4px solid var(--blue)}
.tile .label{position:absolute;left:66px;bottom:6px;font-family:"Ubuntu",sans-serif;font-weight:500;font-size:15px;line-height:16px;color:var(--white)}
.footer{left:0;top:959px;width:741px;height:203px;background:var(--wood)}
.footer .logo{position:absolute;left:46px;top:28px;color:#c79a5c}
.footer .logo i{background:#c79a5c}
.about{position:absolute;left:46px;top:72px;width:196px;font-size:8px;line-height:15px;color:#f3e8d8}
.footer .btn{position:absolute;left:46px;top:157px}
.col{position:absolute;top:25px}
.col h4{font-size:10px;font-weight:600;color:var(--gold);margin-bottom:4px}
.col li{list-style:none;font-size:8.4px;line-height:16.5px;color:#f3e8d8}
.input{position:absolute;left:490px;width:205px;background:var(--white);font-size:7.5px;color:#777;padding:7px 10px;border-radius:2px}
.submit{left:630px;top:1125px;width:65px;height:23px;background:var(--blue);color:var(--white);font-size:8px;font-weight:600;text-align:center;line-height:23px}
.bottombar{left:0;top:1162px;width:741px;height:38px;background:var(--night)}
.bottombar small{position:absolute;left:46px;top:15px;font-size:7px;color:#bdbdbd}
.bottombar .social{position:absolute;left:566px;top:10px}
</style>
</head>
<body>

<header class="abs topbar">
  <div class="social" aria-label="Social links"><span></span><span></span><span></span><span></span><span></span><span></span></div>
  <div class="abs search">Search..
    <svg width="10" height="10" viewBox="0 0 10 10"><circle cx="4" cy="4" r="3" fill="none" stroke="#1b5db4" stroke-width="1.5"/><line x1="6.2" y1="6.2" x2="9.2" y2="9.2" stroke="#1b5db4" stroke-width="1.6"/></svg>
  </div>
</header>

<div class="abs brandband">
  <div class="logo"><i></i>Larch Critter Depot</div>
</div>

<nav class="abs nav">
  <a style="left:52px">HOME</a>
  <a style="left:118px">EVENTS</a>
  <a style="left:190px">BLOG</a>
  <a style="left:253px">ABOUT</a>
  <a style="left:323px">DOG WASH</a>
  <a style="left:409px">PRODUCTS</a>
  <a style="left:495px">RESOURCES</a>
  <a style="left:584px">LINKS</a>
  <a style="left:649px">CONTACT</a>
</nav>

<section class="abs hero">
  <div class="hero-photo" role="img" aria-label="Dog eating kibble from a steel bowl"></div>
  <h1>DEDICATED TO A <b>BETTER DIET</b><br>FOR A <b>HEALTHIER PET</b></h1>
  <div class="dots"><span></span><span></span><span></span><span></span></div>
</section>

<article class="abs card" style="left:49px">
  <h3><i></i>PUP BREW</h3>
  <p>Now you can pour some cold brew for your pup in a fun and easy way that has a delicious flavor and packed full of vegetarian...</p>
  <span class="btn">READ MORE</span>
</article>
<article class="abs card" style="left:268px">
  <h3><i></i>NUTRELO LAWSUIT</h3>
  <p>Nutrelo is being sued by , Dale Ormsby of Cedar Bay, Oregon. He he first purchased Hearthbowl food in December or January. ..</p>
  <span class="btn">READ MORE</span>
</article>
<article class="abs card" style="left:490px">
  <h3><i></i>TIDEWELL 5/8" LEADS ON SALE</h3>
  <p>Your local Tidewell has ALL of their 5/8" Leads ON SALE for just $10!</p>
  <span class="btn">READ MORE</span>
</article>

<div class="abs rule"></div>

<h2 class="abs section-title">LATEST BLOG POSTS</h2>
<div class="abs blog-photo" role="img" aria-label="Before and after photos of a dog's front paws with nail trims circled"></div>
<h3 class="abs blog-title">The Larch Critter Depot Dog Wash News and Updates..</h3>
<div class="abs blog-text">
  <p>The Larch Critter Depot Dog Wash attendants are always here to help wash your four-legged friends, and trim their nails…but they are also here to help educate all of us! Nail trims are such an essential routine for our pups, especially if they don't run and walk as much as they would in the wild.</p>
  <p>Below are two photo that demonstrate how important nail trims are. The 'Before' shot shows the dogs two front feet. Looking at the photo the left foot ( Dogs right foot) has not been trimmed yet. Notice the two outside toes twisting out and away from the foot. The right foot ( Dogs left foot ) has already been trimmed. Notice how "cat like" the toes are, tight and together allowing the pads full access to the ground in a healthy way.</p>
  <span class="btn" style="margin-top:12px">READ MORE</span>
</div>

<aside class="abs newsletter">
  <h2>NEWSLETTER SIGN UP</h2>
  <div class="field">Enter Email</div>
  <span class="dark-btn">SIGN UP</span>
</aside>

<div class="abs tile" style="top:674px">
  <div class="photo" role="img" aria-label="Volunteer with a happy dog at the community food bank" style="background:linear-gradient(90deg,#9a4a3c,#c9b8a4 45%,#6b4a2e)"></div>
  <div class="band"></div><div class="badge"></div>
  <div class="label">Kindle Community<br>Food Bank</div>
</div>
<div class="abs tile" style="top:806px">
  <div class="photo" role="img" aria-label="Terrier holding a leash in its mouth" style="background:linear-gradient(90deg,#d9d6d2,#b28a62 50%,#e2dfda)"></div>
  <div class="band"></div><div class="badge"></div>
  <div class="label">Share With Us!<br>#larchcritter</div>
</div>

<footer class="abs footer">
  <div class="logo"><i></i>Larch Critter Depot</div>
  <p class="about">We are a locally owned and operated premium natural pet food store and supply company. The whole idea for Larch Critter Depot started back in 1993 when Marla Quinn's (owner) dog became sick due to a food allergy.</p>
  <span class="btn">READ MORE</span>
  <div class="col" style="left:278px"><h4>QUICK LINKS</h4><ul><li>Home</li><li>Events</li><li>Blog</li><li>About</li><li>Dog Wash</li><li>Products</li><li>Resources</li><li>Links</li><li>Contact</li></ul></div>
  <div class="col" style="left:385px"><h4>POLICIES</h4><ul><li>Contact</li><li>Return Policy</li><li>Privacy Policy</li><li>Employment</li><li>Staff Login</li></ul></div>
  <div class="col" style="left:490px"><h4>CONTACT US</h4></div>
</footer>
<div class="input" style="top:1006px;height:24px">Name</div>
<div class="input" style="top:1034px;height:24px">Email Address</div>
<div class="input" style="top:1062px;height:52px">Message</div>
<div class="abs submit">SUBMIT</div>

<div class="abs bottombar">
  <small>© Copyright 2015 Larch Critter Depot</small>
  <div class="social" aria-label="Social links"><span></span><span></span><span></span><span></span><span></span><span></span></div>
</div>

</body>
</html>
```